Improved Business Card, Government Contracting

We are looking to update the design of our business cards. We would like to create a template that can be used for future employees and easy to update.

Halvorsen Advisory Partners, LLC is a Service Disabled Veteran Owned Small Business with headquarters located in Leavenworth, KS. Our current website is www.hvadpt.com. We have contracts in KS and VA with expansion opportunities in various other states. Our primary line of work is within government contracting and providing consulting services to various organizations within the Bureau of Civic Readiness. We would like to project a professional image of our company that is consistent with the industry. Provided are previous versions of our business card template that shows our logo as well. We would like to make sure the information on the cards are easily noticeable .

Target Market(s)

Government Officials
Fellow Small Business Contractors
Large Business Contractors (ex. TQLB, Pellwick Darrow, Fenwey Marsh Colquitt)

Industry/Entity Type

Business

Contact Information for Business Card

Dale Forsyth
Office Manager
Halvorsen Advisory Partners
Ph: 555.204.7716
Email: d.forsyth@hvadpt.us
www.hvadpt.com

Requirements
Must have
• The business mailing address is:
• 48730 212th Crescent
• Leavenworth, KS 66091
Nice to have
• Embossed lettering

```html
<!DOCTYPE html>
<html lang="en">
<head>
<meta charset="utf-8">
<title>Halvorsen Advisory Partners – Business Card</title>
<link rel="stylesheet" href="https://fonts.googleapis.com/css2?family=Source+Sans+3:ital,wght@0,400;0,600;0,700;1,400&display=swap">
<style>
  :root {
    --brand-blue: #3b5ba7;
    --ink-blue: #3a58a3;
    --accent-gold: #fcc30b;
    --card-white: #ffffff;
  }
  html, body {
    margin: 0;
    padding: 0;
    width: 1200px;
    height: 683px;
    overflow: hidden;
    background: var(--card-white);
  }
  .business-card {
    position: relative;
    width: 1200px;
    height: 683px;
    background: var(--card-white);
    font-family: "Source Sans 3", "Myriad Pro", sans-serif;
    color: var(--ink-blue);
    overflow: hidden;
  }
  .brand-band {
    position: absolute;
    left: 0;
    top: 193px;
    width: 1200px;
    height: 108px;
    background: var(--brand-blue);
  }
  .company-lockup {
    position: absolute;
    left: 0;
    top: 193px;
    width: 1200px;
    height: 108px;
    display: flex;
    align-items: center;
    justify-content: center;
    gap: 26px;
  }
  .company-mark {
    width: 40px;
    height: 40px;
    background: var(--accent-gold);
    flex: none;
  }
  .company-name {
    margin: 0;
    font-size: 70px;
    font-weight: 600;
    letter-spacing: 1px;
    color: var(--card-white);
    line-height: 1;
  }
  .person {
    position: absolute;
    right: 703px;
    top: 466px;
    text-align: right;
    line-height: 1;
  }
  .person-name {
    margin: 0;
    font-size: 48px;
    font-weight: 700;
  }
  .person-title {
    margin: 10px 0 0;
    font-size: 32px;
    font-style: italic;
    font-weight: 400;
  }
  .mailing-address {
    margin: 18px 0 0;
    font-size: 26px;
    font-style: normal;
    font-weight: 400;
    line-height: 1.25;
  }
  .contact {
    position: absolute;
    left: 703px;
    top: 478px;
    margin: 0;
    font-size: 34px;
    line-height: 1;
  }
  .contact-row {
    display: flex;
    margin: 0 0 11px;
  }
  .contact-label {
    width: 67px;
    font-weight: 700;
  }
  .contact-value {
    font-weight: 400;
    letter-spacing: 0.5px;
  }
  .contact-web {
    margin-top: 3px;
    font-size: 36px;
    font-weight: 700;
  }
</style>
</head>
<body>
  <main class="business-card">
    <div class="brand-band"></div>
    <div class="company-lockup">
      <span class="company-mark"></span>
      <h1 class="company-name">Halvorsen Advisory Partners</h1>
    </div>

    <section class="person">
      <p class="person-name">Dale Forsyth</p>
      <p class="person-title">Office Manager</p>
      <address class="mailing-address">48730 212th Crescent<br>Leavenworth, KS 66091</address>
    </section>

    <section class="contact">
      <div class="contact-row"><span class="contact-label">P:</span><span class="contact-value">555.204.7716</span></div>
      <div class="contact-row"><span class="contact-label">E:</span><span class="contact-value">d.forsyth@hvadpt.us</span></div>
      <div class="contact-web">www.hvadpt.com</div>
    </section>
  </main>
</body>
</html>
```